Brindle Yard Care. The best in the biz

I run a lawn care service that offers full service mowing. 100% satisfaction guarantee. Fast, Friendly, quality service "I am your lawns best friend" I cut residential lawns. I offer a mow package that includes trimming, edging and clean up. Prices very from 20 dollars to 75. I want my logo to stand out. Free estimates

Target Market(s)

Home owners

Industry/Entity Type

Landscaping

Contact Information for Business Card

555-812-4473 tomvale48@quillmail.net Derek. Brindle Yard care

Colors
f37122
9bcb3c
cadf82

Requirements
Must have
• Company name.
• Phone number
• Email
• My services
• images
Nice to have
• A sun that is growing grass.
Should not have
• Incorrect information

```html
<!DOCTYPE html>
<html lang="en">
<head>
<meta charset="utf-8">
<title>Brindle Yard Care – Business Card</title>
<link rel="stylesheet" href="https://fonts.googleapis.com/css2?family=Open+Sans:wght@400;600;700&family=Roboto:wght@400&display=swap">
<style>
  :root {
    --stage-top: #2b2b2b;
    --stage-bottom: #050505;
    --card: #ffffff;
    --green: #8cc63f;
    --orange: #f26a1b;
    --ink: #4a4a4a;
    --slate: #5f5f5f;
  }
  * { margin: 0; padding: 0; box-sizing: border-box; }
  html, body { width: 1200px; height: 900px; overflow: hidden; }
  body {
    background: linear-gradient(to bottom, var(--stage-top), var(--stage-bottom));
    font-family: "Open Sans", Arial, sans-serif;
    position: relative;
  }
  .card {
    position: absolute;
    top: 306px;
    height: 271px;
    background: var(--card);
    border-radius: 12px;
  }
  .card--front { left: 149px; width: 439px; }
  .card--back { left: 608px; width: 441px; text-align: center; }

  .brand-mark {
    position: absolute;
    left: 200px;
    top: 0;
  }
  .card--front .brand-mark {
    left: 50px;
    top: 62px;
    width: 152px;
    text-align: center;
  }
  .brand-dot {
    display: block;
    width: 104px;
    height: 104px;
    margin: 0 auto 12px;
    border-radius: 50%;
    background: var(--green);
  }
  .brand-name {
    font-weight: 600;
    font-size: 15px;
    color: var(--green);
    white-space: nowrap;
  }

  .contact {
    position: absolute;
    left: 247px;
    top: 98px;
  }
  .contact-name {
    font-weight: 700;
    font-size: 15px;
    color: var(--green);
    margin-bottom: 18px;
  }
  .contact-line {
    display: flex;
    align-items: center;
    gap: 7px;
    font-size: 12.5px;
    color: var(--ink);
    line-height: 16px;
  }
  .contact-line svg { width: 9px; height: 9px; fill: var(--green); }

  .card--back .brand-dot {
    position: absolute;
    left: 170px;
    top: 26px;
    width: 90px;
    height: 90px;
    margin: 0;
  }
  .company {
    position: absolute;
    left: 0; right: 0;
    top: 120px;
    font-family: "Roboto", Arial, sans-serif;
    font-size: 34px;
    color: var(--green);
  }
  .promises {
    position: absolute;
    left: 0; right: 0;
    top: 173px;
    list-style: none;
  }
  .promises li {
    font-weight: 600;
    font-size: 13.5px;
    color: var(--orange);
    text-transform: uppercase;
    line-height: 29px;
  }
</style>
</head>
<body>
  <section class="card card--front">
    <div class="brand-mark">
      <span class="brand-dot"></span>
      <span class="brand-name">Brindle Yard Care</span>
    </div>
    <div class="contact">
      <p class="contact-name">Derek</p>
      <p class="contact-line">
        <svg viewBox="0 0 10 10" aria-hidden="true"><path d="M2 0.5 3.6 2.6 2.7 3.6C3.3 5 4.9 6.6 6.4 7.3L7.4 6.4 9.5 8 8.4 9.5C4.5 9.3.7 5.5.5 1.6Z"/></svg>
        555-812-4473
      </p>
      <p class="contact-line">
        <svg viewBox="0 0 10 10" aria-hidden="true"><path d="M0.5 2h9v6.5h-9z"/><path d="M0.8 2.3 5 5.6 9.2 2.3" fill="none" stroke="#fff" stroke-width="0.9"/></svg>
        tomvale48@quillmail.net
      </p>
    </div>
  </section>

  <section class="card card--back">
    <span class="brand-dot"></span>
    <h1 class="company">Brindle Yard Care</h1>
    <ul class="promises">
      <li>100% Satisfaction Guarantee.</li>
      <li>Fast, Friendly, Quality Service</li>
      <li>I am your lawns best friend</li>
    </ul>
  </section>
</body>
</html>
```